New Business Card Design Project

I need a design for business cards, i am an electrical business called "Corvane Electrical and Communications" i need the cards to be double sided with the company logo on the back (attached) the front needs to say my company name, web site, email address, telephone number, and ABN number and electrical license number. I am open to different arrangements of the information but would like the background to be incorporating something electrical or something that looks smart. open to all additional ideas also.

The company colours are orange and grey see logo attached.

Business Name: Corvane Electrical and Communications
Website: corvaneelectricalandcomms.example.com.au
Email: brent@corvaneelectricalandcomms.example.com.au
Telephone(mobile): 0481209736
ABN: 71208349162
Lic No: 418273D

Target Market(s)

Business entities, Project Managers, Accounts, Clients

Industry/Entity Type

Electrician

Contact Information for Business Card

I need a design for business cards, i am an electrical business called "Corvane Electrical and Communications" i need the cards to be double sided with the company logo on the back (attached) the front needs to say my company name

Font styles to use
Serif
Sans Serif

Colors
f37122
5c5c5c

Requirements
Must have
• Must have the Logo on the back open to different ways of it being on the back but had in mind to keep it central but again open to other options
Nice to have
• A real modern cool background that is eye catching yet contemporary
Should not have
• No backgrounds of a light bulb or plug or anything like that

```html
<!DOCTYPE html>
<html lang="en">
<head>
<meta charset="utf-8">
<title>Corvane Electrical and Communications – Business Card</title>
<link href="https://fonts.googleapis.com/css2?family=Arimo:wght@400;700&display=swap" rel="stylesheet">
<style>
  :root {
    --page-bg: #e6e6e6;
    --card-dark: #3a3a3c;
    --card-mid: #5c5c5c;
    --card-light: #6a6a6b;
    --orange: #f3a622;
    --orange-deep: #e8961a;
    --band-white: #f2f2f2;
    --band-grey: #cfcfcf;
    --text-light: #f4f4f4;
    --text-muted: #c9c9c9;
  }
  * { margin: 0; padding: 0; box-sizing: border-box; }
  html, body {
    width: 1200px; height: 950px; overflow: hidden;
    background: var(--page-bg);
    font-family: "Arimo", Arial, sans-serif;
  }
  .canvas {
    position: relative; width: 1200px; height: 950px;
  }
  .card {
    position: absolute; left: 270px; width: 660px; height: 403px;
    border-radius: 4px; overflow: hidden;
    box-shadow: 0 10px 28px rgba(0,0,0,0.25);
    background: linear-gradient(100deg, var(--card-dark) 0%, var(--card-mid) 55%, var(--card-light) 100%);
  }
  .card-back { top: 48px; }
  .card-front { top: 499px; }

  .sheen {
    position: absolute; top: 0; bottom: 0; left: 56%; width: 40px;
    background: linear-gradient(90deg, rgba(255,255,255,0) 0%, rgba(255,255,255,0.12) 50%, rgba(255,255,255,0) 100%);
  }

  /* Back */
  .back-brand {
    position: absolute; left: 0; right: 0; top: 150px;
    display: flex; justify-content: center; align-items: center; gap: 14px;
  }
  .brand-dot {
    width: 16px; height: 16px; border-radius: 50%; background: var(--orange);
  }
  .brand-name {
    font-weight: 700; color: var(--orange); letter-spacing: 0.5px;
  }
  .back-brand .brand-name { font-size: 30px; }
  .back-web {
    position: absolute; left: 0; right: 0; top: 232px;
    text-align: center; color: var(--text-muted); font-size: 17px; letter-spacing: 0.5px;
  }

  /* Front */
  .front-brand {
    position: absolute; left: 42px; top: 50px;
    display: flex; align-items: center; gap: 10px;
  }
  .front-brand .brand-name { font-size: 19px; }
  .contact-list {
    position: absolute; left: 42px; top: 148px; list-style: none;
    color: var(--text-light); font-size: 17px; line-height: 29px;
  }
  .contact-list li { display: flex; align-items: center; gap: 8px; }
  .contact-icon { width: 15px; height: 15px; flex: none; }

  .name-band, .role-band {
    position: absolute; top: 0; bottom: 0; width: 62px;
    display: flex; align-items: center; justify-content: center;
  }
  .name-band {
    right: 62px;
    background: linear-gradient(90deg, var(--band-grey), var(--band-white) 60%);
  }
  .role-band {
    right: 0;
    background: linear-gradient(90deg, var(--orange-deep), var(--orange));
  }
  .band-text {
    transform: rotate(-90deg); white-space: nowrap; font-size: 18px; letter-spacing: 0.5px;
  }
  .holder-name { color: var(--orange-deep); }
  .holder-role { color: var(--text-light); }
</style>
</head>
<body>
<main class="canvas">

  <section class="card card-back" aria-label="Card back">
    <div class="sheen"></div>
    <div class="back-brand">
      <span class="brand-dot"></span>
      <span class="brand-name">Corvane Electrical &amp; Communications</span>
    </div>
    <p class="back-web">corvaneelectricalandcomms.example.com.au</p>
  </section>

  <section class="card card-front" aria-label="Card front">
    <div class="sheen"></div>
    <div class="front-brand">
      <span class="brand-dot"></span>
      <span class="brand-name">Corvane Electrical &amp; Communications</span>
    </div>
    <ul class="contact-list">
      <li>ABN: 71208349162</li>
      <li>Lic No: 418273D</li>
      <li>
        <svg class="contact-icon" viewBox="0 0 16 16" aria-hidden="true"><rect x="4" y="1" width="8" height="14" rx="1.5" fill="none" stroke="#f3a622" stroke-width="1.6"/><circle cx="8" cy="12.5" r="0.9" fill="#f3a622"/></svg>
        0481209736
      </li>
      <li>
        <svg class="contact-icon" viewBox="0 0 16 16" aria-hidden="true"><rect x="1" y="3" width="14" height="10" rx="1" fill="#f3a622"/><path d="M1.5 3.5 L8 9 L14.5 3.5" fill="none" stroke="#4a4a4a" stroke-width="1.3"/></svg>
        brent@corvaneelectricalandcomms.example.com.au
      </li>
      <li>
        <svg class="contact-icon" viewBox="0 0 16 16" aria-hidden="true"><circle cx="8" cy="8" r="7" fill="#f3a622"/><path d="M1 8 H15 M8 1 C5 4 5 12 8 15 M8 1 C11 4 11 12 8 15" fill="none" stroke="#4a4a4a" stroke-width="1.1"/></svg>
        corvaneelectricalandcomms.example.com.au
      </li>
    </ul>
    <div class="name-band"><span class="band-text holder-name">MARLO VANCE</span></div>
    <div class="role-band"><span class="band-text holder-role">PRESIDENT</span></div>
  </section>

</main>
</body>
</html>
```